business card - for laser marking

I need design (curve) for my business card (make with laser) size 85mm x 55mm. How it look business card with laser marking see attached picture.

color:
Background: white
text and icons black

Please include: one side
1. dominik vrabec - direktor
2. phone: +386(0)41 726 190
+386(0)580 237 61
3. info@zarezko.example
4. faecebook.com/Zarezko.Ex
5. KM-ATELJE, Dominik Vrabec s.p.
Lipova ulica 19, 1000 Ljubljana, SI
6. logo

Please include: second side
1. logo
2. www.zarezko.example
3. Lasersko graviranje
ovitki telefonov, ohišja telefonov / tablic, nakit, ure, alu vizitke, dog-tagi, kemični svinčniki, orodja, noži, vžigalniki

Industry/Entity Type

Business

Contact Information for Business Card

Please include: one side
+386(0)580 237 61
3. info@zarezko.example
6. logo

1. logo
2. www.zarezko.example
3. Lasersko graviranje

Colors
000000
ffffff

Requirements
Must have
• I need design (curve) for my business card (make with laser) size 85mm x 55mm. How it look business card with laser marking see attached picture.
• color:
• Background: white
• text and icons black
• Please include: one side
• 1. dominik vrabec - direktor
• 2. phone: +386(0)41 726 190
• +386(0)580 237 61
• 3. info@zarezko.example
• 4. faecebook.com/Zarezko.Ex
• 5. KM-ATELJE, Dominik Vrabec s.p.
• Lipova ulica 19, 1000 Ljubljana, SI
• 6. logo
• Please include: second side
• 1. logo
• 2. www.zarezko.example
• 3. Lasersko graviranje
• ovitki telefonov, ohišja telefonov / tablic, nakit, ure, alu vizitke, dog-tagi, kemični svinčniki, orodja, noži, vžigalniki

```html
<!DOCTYPE html>
<html lang="sl">
<head>
<meta charset="utf-8">
<title>Zarezko – vizitka</title>
<link rel="stylesheet" href="https://fonts.googleapis.com/css2?family=Roboto:wght@400;500;700&display=swap">
<style>
  :root {
    --backdrop: #e9e6e2;
    --card: #ffffff;
    --ink: #000000;
    --splash-dark: #bdbdbd;
    --splash-light: #f2f2f2;
  }
  * { margin: 0; padding: 0; box-sizing: border-box; }
  html, body {
    width: 1200px; height: 960px; overflow: hidden;
    background: var(--backdrop);
    font-family: "Roboto", Arial, sans-serif;
  }
  .canvas { position: relative; width: 1200px; height: 960px; }

  .card {
    position: absolute; left: 320px; width: 600px;
    border-radius: 18px; overflow: hidden;
    background: var(--card); color: var(--ink);
  }
  .card--front { top: 100px; height: 348px; text-align: center; }
  .card--back { top: 493px; height: 342px; }

  /* front side */
  .brand-mark {
    position: absolute; top: 130px; left: 0; width: 100%;
    display: flex; justify-content: center; align-items: center; gap: 10px;
  }
  .brand-mark__dot { width: 14px; height: 14px; border-radius: 50%; background: var(--ink); }
  .brand-mark__name { font-size: 30px; font-weight: 700; letter-spacing: 2px; color: var(--ink); }
  .services {
    position: absolute; top: 247px; left: 0; width: 100%;
    font-size: 15px; line-height: 18px;
  }
  .website {
    position: absolute; top: 308px; left: 0; width: 100%;
    font-size: 17px; font-weight: 500;
  }

  /* back side */
  .contact-panel {
    position: absolute; left: 0; top: 0; width: 348px; height: 100%;
    padding: 36px 0 0 33px;
  }
  .person__name { font-size: 20px; font-weight: 700; line-height: 22px; }
  .person__role { font-size: 14px; font-weight: 700; line-height: 20px; margin-top: 2px; }
  .company { margin-top: 78px; font-size: 14px; line-height: 18px; }
  .contact-list { list-style: none; margin-top: 8px; font-size: 14px; line-height: 19px; }
  .contact-list li { display: flex; align-items: center; gap: 8px; }
  .contact-list svg { width: 14px; height: 14px; flex: none; fill: var(--ink); }
  .splash-area {
    position: absolute; left: 348px; top: 0; width: 252px; height: 100%;
    background: linear-gradient(100deg, var(--splash-dark) 0%, #dcdcdc 40%, var(--splash-light) 80%, var(--card) 100%);
  }
</style>
</head>
<body>
<main class="canvas">
  <section class="card card--front">
    <div class="brand-mark">
      <span class="brand-mark__dot"></span>
      <span class="brand-mark__name">ZAREZKO</span>
    </div>
    <p class="services">
      Lasersko graviranje<br>
      ovitki telefonov, ohišja telefonov / tablic, nakit, ure, alu vizitke<br>
      dog-tagi, kemicni svincniki, orodja, noži, vžigalniki
    </p>
    <p class="website">www.zarezko.example</p>
  </section>

  <section class="card card--back">
    <div class="contact-panel">
      <h1 class="person__name">DOMINIK VRABEC</h1>
      <p class="person__role">DIREKTOR</p>
      <p class="company">
        KM-ATELJE<br>
        Dominik Vrabec s.p.<br>
        Lipova ulica 19<br>
        1000 Ljubljana, SI
      </p>
      <ul class="contact-list">
        <li>
          <svg viewBox="0 0 16 16"><path d="M3.5 1.5l2.6 2.6-1.5 2a8 8 0 0 0 5.3 5.3l2-1.5 2.6 2.6-1.6 2C7.4 14.8 1.2 8.6 1.5 3.1z"/></svg>
          +386(0)580 237 61
        </li>
        <li>
          <svg viewBox="0 0 16 16"><path d="M4 0h8a1 1 0 0 1 1 1v14a1 1 0 0 1-1 1H4a1 1 0 0 1-1-1V1a1 1 0 0 1 1-1zm1 2v10h6V2zm3 11a1 1 0 1 0 0 2 1 1 0 0 0 0-2z"/></svg>
          +386(0)41 726 190
        </li>
        <li>
          <svg viewBox="0 0 16 16"><path d="M1 3h14v1.2L8 9 1 4.2zm0 2.6l7 4.8 7-4.8V13H1z"/></svg>
          info@zarezko.example
        </li>
        <li>
          <svg viewBox="0 0 16 16"><rect x="1" y="1" width="14" height="14" rx="1"/></svg>
          Zarezko.Ex
        </li>
      </ul>
    </div>
    <div class="splash-area" role="img" aria-label="Decorative engraved paint splash"></div>
  </section>
</main>
</body>
</html>
```